Brell Stone Company Business Cards

Front and Back Business Card - logo and text setup - cool design. I need workable photoshop or illustrator files so I can setup each employee card with design that is created
Updates

Hi everyone, thank you for the great entries. Please no more white and blue cards - there are so many already - black and silver only now please. thanks!

Target Market(s)

Construction Industry - Facility Managers

Industry/Entity Type

Construction

Contact Information for Business Card

I really like contemporary simplistic looks - clean neat....not opposed to seeing some black backrounds

Requirements
Must have
• Logo/website address with design on front only - www.brellstone-example.com (logo attached)
• Back:
• Name/Title/Company Address/Phone/email address
Nice to have
• Cool design
Should not have
• Nothing gimmicky like Fire or Water - since we are a Fire Protection company - it has all been done

```html
<!DOCTYPE html>
<html lang="en">
<head>
<meta charset="utf-8">
<title>Brell Stone Company – Business Cards</title>
<link rel="stylesheet" href="https://fonts.googleapis.com/css2?family=Lato:wght@400;900&display=swap">
<style>
  :root {
    --backdrop: #3a3a3c;
    --card-black: #111112;
    --card-black-soft: #1c1c1e;
    --silver: #c9cbce;
    --silver-bright: #e6e7e9;
    --silver-dim: #9a9da2;
    --rule-silver: #5c5e62;
    --graphite: #2a2b2e;
  }
  * { margin: 0; padding: 0; box-sizing: border-box; }
  html, body { width: 1200px; height: 1200px; overflow: hidden; }
  body {
    background: var(--backdrop);
    font-family: "Lato", sans-serif;
    position: relative;
  }
  .card {
    position: absolute;
    top: 310px;
    width: 364px;
    height: 594px;
    box-shadow: 0 6px 18px rgba(0,0,0,0.55);
    overflow: hidden;
  }
  .card--contact {
    left: 234px;
    background: var(--card-black);
    text-align: center;
  }
  .card--brand { left: 628px; width: 368px; }

  .wordmark {
    position: absolute;
    left: 0; right: 0;
    font-weight: 900;
    color: var(--silver-bright);
    letter-spacing: -1px;
    text-align: center;
    line-height: 1;
    white-space: nowrap;
  }
  .card--contact .wordmark { top: 142px; font-size: 52px; }
  .card--brand .wordmark { top: 262px; font-size: 54px; }

  .person { position: absolute; top: 334px; left: 0; right: 0; }
  .person__name { font-size: 22px; line-height: 26px; color: var(--silver-bright); letter-spacing: 0.2px; }
  .person__name .surname { color: var(--silver-dim); }
  .person__title { font-size: 17px; line-height: 22px; color: var(--silver); margin-top: 0; }

  .icon-row {
    position: absolute; top: 395px; left: 87px;
    width: 190px; height: 26px;
  }
  .contact-lines {
    position: absolute; top: 431px; left: 0; right: 0;
    font-size: 17px; line-height: 22px; color: var(--silver);
  }
  .divider {
    position: absolute; top: 506px; left: 89px; width: 194px;
    border-top: 1px solid var(--rule-silver);
  }
  .address {
    position: absolute; top: 517px; left: 0; right: 0;
    font-size: 17px; line-height: 22px; color: var(--silver);
  }

  .brand-backdrop {
    position: absolute; inset: 0;
    background:
      radial-gradient(ellipse at 35% 35%, rgba(150,152,158,0.55) 0%, rgba(150,152,158,0) 60%),
      linear-gradient(160deg, var(--graphite) 0%, #3d3f43 45%, var(--card-black) 100%);
  }
  .brand-url {
    position: absolute; top: 530px; left: 0; right: 0;
    text-align: center; font-size: 19px; color: var(--silver-bright);
  }
</style>
</head>
<body>

  <section class="card card--contact">
    <div class="wordmark">Brell Stone</div>

    <div class="person">
      <div class="person__name">MARCUS <span class="surname">HALE</span></div>
      <div class="person__title">Managing Director</div>
    </div>

    <svg class="icon-row" viewBox="0 0 190 26" aria-hidden="true">
      <line x1="0" y1="13" x2="52" y2="13" stroke="var(--rule-silver)" stroke-width="1.5"/>
      <line x1="138" y1="13" x2="190" y2="13" stroke="var(--rule-silver)" stroke-width="1.5"/>
      <circle cx="68" cy="13" r="12" fill="var(--silver)"/>
      <path d="M63 8 q-2 6 4 11 q4 3 7 1 l-1.5 -3 l-2.5 1 q-3 -2 -4 -5 l1.5 -2 z" fill="var(--card-black)"/>
      <circle cx="95" cy="13" r="12" fill="var(--silver)"/>
      <rect x="88" y="8" width="14" height="10" fill="var(--card-black)"/>
      <path d="M88 8 l7 6 l7 -6" fill="none" stroke="var(--silver)" stroke-width="1.3"/>
      <circle cx="122" cy="13" r="12" fill="var(--silver)"/>
      <circle cx="122" cy="13" r="6.5" fill="none" stroke="var(--card-black)" stroke-width="1.4"/>
      <ellipse cx="122" cy="13" rx="2.8" ry="6.5" fill="none" stroke="var(--card-black)" stroke-width="1.2"/>
      <line x1="115.5" y1="13" x2="128.5" y2="13" stroke="var(--card-black)" stroke-width="1.2"/>
    </svg>

    <div class="contact-lines">
      <div>044-555 010 234</div>
      <div>hello@brellstone-example.com</div>
      <div>www.brellstone-example.com</div>
    </div>
    <div class="divider"></div>
    <div class="address">
      <div>421, Address line here,</div>
      <div>45452,Country Name</div>
    </div>
  </section>

  <section class="card card--brand">
    <div class="brand-backdrop" role="img" aria-label="Decorative diagonal grid of small silver and graphite tiles on a dark gradient"></div>
    <div class="wordmark">Brell Stone</div>
    <div class="brand-url">www.brellstone-example.com</div>
  </section>

</body>
</html>
```